Boutique custom software development company needs new business card

Our nearly 20 year old custom software development company would like to better include the fact that we are now providing Bitcoin services. These new services are B2B include education (how to acquire and securely hold Bitcoin) and integrating Bitcoin payments into existing ecommerce sites or other existing systems. Please keep the card clean and simple. Attached is our current design and some other files. vextorial.com

Target Market(s)

businesses owners interested in long term relationship

Industry/Entity Type

Custom software development and Bitcoin

Contact Information for Business Card

Dale Parker, dale@vextorial.com, vextorial.com, (888) 555-VXTRL

Font styles to use
Other font styles liked:
• monospace

Requirements
Must have
• double-sided
Nice to have
• clean and simple
Should not have
• physical address

```html
<!DOCTYPE html>
<html lang="en">
<head>
<meta charset="utf-8">
<title>Vextorial Business Card</title>
<link href="https://fonts.googleapis.com/css2?family=Montserrat:wght@400;500;700&family=Lato:wght@400&display=swap" rel="stylesheet">
<style>
  :root {
    --brand-blue: #4174b9;
    --band-blue: #3b72b6;
    --brand-orange: #ef7a24;
    --brand-yellow: #fbbc15;
    --ink: #111111;
    --paper: #ffffff;
  }
  * { margin: 0; padding: 0; box-sizing: border-box; }
  html, body { width: 1200px; height: 1200px; overflow: hidden; }
  body { position: relative; background: var(--paper); font-family: 'Montserrat', sans-serif; }

  .backdrop-top { position: absolute; left: 0; top: 0; width: 1200px; height: 586px; background: var(--brand-blue); }
  .stripe-orange { position: absolute; left: 0; top: 586px; width: 1200px; height: 14px; background: var(--brand-orange); }
  .stripe-yellow { position: absolute; left: 0; top: 600px; width: 1200px; height: 13px; background: var(--brand-yellow); }

  .card { position: absolute; left: 237px; width: 726px; height: 420px; }
  .card-front { top: 86px; background: var(--paper); }
  .card-back { top: 690px; background: var(--brand-blue); }

  .wordmark {
    position: absolute; left: 0; width: 100%; text-align: center;
    font-family: 'Montserrat', sans-serif; font-weight: 700; letter-spacing: 1px;
  }
  .card-front .wordmark { top: 104px; font-size: 58px; line-height: 64px; color: var(--brand-blue); }
  .card-back .wordmark { top: 156px; font-size: 66px; line-height: 72px; color: var(--paper); }

  .tagline {
    position: absolute; left: 0; width: 100%; text-align: center;
    font-family: 'Lato', sans-serif; letter-spacing: -0.8px;
  }
  .card-front .tagline { top: 166px; font-size: 19px; color: var(--brand-blue); }
  .card-back .tagline { top: 232px; font-size: 23px; color: var(--paper); }

  .identity { position: absolute; right: 337px; top: 240px; text-align: right; }
  .person-name { font-size: 40px; font-weight: 700; line-height: 44px; letter-spacing: 0.5px; white-space: nowrap; }
  .person-name .first { color: var(--brand-orange); }
  .person-name .last { color: var(--brand-blue); }
  .person-email { font-size: 18.5px; font-weight: 500; color: var(--ink); letter-spacing: 1px; margin-top: 2px; white-space: nowrap; }

  .divider { position: absolute; left: 417px; top: 247px; width: 2px; height: 55px; background: var(--brand-blue); }

  .contact-line { position: absolute; left: 437px; display: flex; align-items: center; gap: 12px; font-size: 18.5px; font-weight: 500; color: var(--ink); letter-spacing: 1px; white-space: nowrap; }
  .contact-phone { top: 244px; }
  .contact-web { top: 278px; }
  .contact-line svg { width: 22px; height: 22px; flex: none; }

  .services-band {
    position: absolute; left: 0; top: 361px; width: 100%; height: 36px; background: var(--band-blue);
    display: flex; align-items: center; justify-content: center;
    color: var(--paper); font-size: 18px; font-weight: 500; letter-spacing: 0.6px; white-space: nowrap;
  }
</style>
</head>
<body>
  <div class="backdrop-top"></div>
  <div class="stripe-orange"></div>
  <div class="stripe-yellow"></div>

  <section class="card card-front">
    <div class="wordmark">VEXTORIAL</div>
    <div class="tagline">developer of custom applications</div>

    <div class="identity">
      <div class="person-name"><span class="first">Dale</span> <span class="last">Parker</span></div>
      <div class="person-email">dale@vextorial.com</div>
    </div>

    <div class="divider"></div>

    <div class="contact-line contact-phone">
      <svg viewBox="0 0 24 24" fill="none" stroke="#4174b9" stroke-width="1.6">
        <rect x="6.5" y="2" width="11" height="20" rx="2"/>
        <line x1="10" y1="4.5" x2="14" y2="4.5"/>
        <circle cx="12" cy="18.5" r="0.8" fill="#4174b9"/>
      </svg>
      <span>(888) 555-VXTRL</span>
    </div>

    <div class="contact-line contact-web">
      <svg viewBox="0 0 24 24" fill="none" stroke="#4174b9" stroke-width="1.2">
        <circle cx="12" cy="12" r="10"/>
        <ellipse cx="12" cy="12" rx="4.5" ry="10"/>
        <line x1="2" y1="12" x2="22" y2="12"/>
        <path d="M4 6.5h16M4 17.5h16"/>
        <line x1="12" y1="2" x2="12" y2="22"/>
      </svg>
      <span>vextorial.com</span>
    </div>

    <div class="services-band">Custom Software · Bitcoin Education &amp; Payment Integration</div>
  </section>

  <section class="card card-back">
    <div class="wordmark">VEXTORIAL</div>
    <div class="tagline">developer of custom applications</div>
  </section>
</body>
</html>
```